Business Card Design For A Renovation Contractor Company

We need a business card for a new company based in Singapore, our company name is "RB Tolvane". We are a renovation contractor that builds designs into reality. We build more of F&B restaurants, retail stores and commercial offices. We work very closely with designers. The final design should communicate to our client that we are a company that you can trust, that will plan and complete your project without giving you a headache. I like my client to remember my company as "RB". The beauty of SIMPLE is important.

Industry/Entity Type

Contractor

Requirements
Nice to have
• Black or Red base

```html
<!DOCTYPE html>
<html lang="en">
<head>
<meta charset="utf-8">
<title>RB Tolvane — Business Card</title>
<link rel="stylesheet" href="https://fonts.googleapis.com/css2?family=Open+Sans:wght@300;400;600;700&display=swap">
<style>
  :root {
    --bg: #e9e9ee;
    --card-white: #ffffff;
    --card-black: #050505;
    --ink: #1a1a1a;
    --red: #d81f26;
    --muted-grey: #2b2b2b;
    --faint: #f0eded;
    --faint-edge: #f6d9da;
    --text-white: #f4f4f4;
    --contact-ink: #333333;
  }
  * { margin: 0; padding: 0; box-sizing: border-box; }
  html, body {
    width: 1200px; height: 987px; overflow: hidden;
    background: var(--bg);
    font-family: "Open Sans", Arial, sans-serif;
  }
  .stage { position: relative; width: 1200px; height: 987px; }

  .card {
    position: absolute;
    width: 640px; height: 366px;
    border-radius: 34px;
    overflow: hidden;
    box-shadow: 0 10px 30px rgba(0,0,0,0.12);
  }

  /* Back side */
  .card-back { left: 500px; top: 70px; background: var(--card-black); }
  .card-back .emblem-ring {
    position: absolute; right: -40px; top: 60px;
    width: 340px; height: 340px; border-radius: 50%;
    border: 34px solid var(--muted-grey);
  }
  .card-back .wordmark {
    position: absolute; left: 48px; top: 118px;
    color: var(--text-white);
  }
  .wordmark .name {
    display: block;
    font-weight: 300;
    font-size: 56px;
    letter-spacing: -1px;
    line-height: 1;
  }
  .wordmark .tagline {
    display: block;
    margin-top: 8px;
    padding-top: 2px;
    border-top: 1px solid currentColor;
    font-weight: 300;
    font-size: 19px;
    letter-spacing: 0.5px;
  }

  /* Front side */
  .card-front { left: 60px; top: 540px; background: var(--card-white); }
  .card-front .emblem-ring {
    position: absolute; right: 40px; top: 70px;
    width: 360px; height: 360px; border-radius: 50%;
    border: 32px solid var(--faint);
    outline: 1px solid var(--faint-edge);
  }
  .card-front .brand-row {
    position: absolute; left: 40px; top: 34px;
    display: flex; align-items: flex-end; gap: 14px;
  }
  .card-front .brand-dot {
    width: 46px; height: 46px; border-radius: 50%;
    background: var(--red);
    margin-bottom: 30px;
  }
  .card-front .wordmark { color: var(--ink); }
  .card-front .wordmark .name { font-size: 46px; }
  .card-front .wordmark .tagline { font-size: 16px; }

  .person { position: absolute; left: 44px; top: 140px; }
  .person .full-name { font-weight: 700; font-size: 20px; color: var(--ink); }
  .person .role { font-size: 15px; color: var(--red); }

  .website {
    position: absolute; left: 44px; top: 240px;
    font-size: 18px; letter-spacing: 4px; color: var(--ink);
  }
  .website .accent { color: var(--red); font-weight: 600; }

  .contact {
    position: absolute; left: 360px; top: 212px;
    list-style: none; font-size: 15px; color: var(--contact-ink); line-height: 1.35;
  }
  .contact li { display: flex; gap: 8px; align-items: flex-start; margin-bottom: 3px; }
  .contact svg { flex: none; width: 14px; height: 14px; margin-top: 3px; fill: var(--red); }
</style>
</head>
<body>
<main class="stage">

  <section class="card card-back" aria-label="Business card back">
    <div class="emblem-ring"></div>
    <div class="wordmark">
      <span class="name">RB Tolvane</span>
      <span class="tagline">built right, built to plan</span>
    </div>
  </section>

  <section class="card card-front" aria-label="Business card front">
    <div class="emblem-ring"></div>

    <div class="brand-row">
      <div class="wordmark">
        <span class="name">RB Tolvane</span>
        <span class="tagline">built right, built to plan</span>
      </div>
      <div class="brand-dot"></div>
    </div>

    <div class="person">
      <p class="full-name">Your Name</p>
      <p class="role">Title</p>
    </div>

    <p class="website">www.<span class="accent">rbtolvane</span>.com</p>

    <ul class="contact">
      <li>
        <svg viewBox="0 0 14 14"><path d="M1 13V6l6-4 6 4v7H9V9H5v4z"/></svg>
        <span>Street Name, City Name<br>State Zip Code</span>
      </li>
      <li>
        <svg viewBox="0 0 14 14"><path d="M3 1l3 3-2 2c1 2 2 3 4 4l2-2 3 3-2 2C6 13 1 8 1 3z"/></svg>
        <span>123-456-0789</span>
      </li>
      <li>
        <svg viewBox="0 0 14 14"><rect x="4" y="1" width="6" height="12" rx="1"/></svg>
        <span>123-456-0789</span>
      </li>
      <li>
        <svg viewBox="0 0 14 14"><path d="M1 3h12v8H1z M1 3l6 5 6-5" /></svg>
        <span>info@rbtolvane.com</span>
      </li>
    </ul>
  </section>

</main>
</body>
</html>
```